Business card update

Opening a subsidiary of my company in the USA and need to update my logo.
Updates

Reason: Give more time to a good design.

I made a mistake on my briefing. It's only the business card. Thanks for alerting me on the mistake.

All the best

Teodoro

Target Market(s)

We are an Executive Search company and our target audience are executives in large corporations.

Industry/Entity Type

Business

Requirements
Must have
• Keep the logo. In the US the company is called Delia Brunet Executive Search.

```html
<!DOCTYPE html>
<html lang="en">
<head>
<meta charset="utf-8">
<title>Delia Brunet Executive Search – Business Card</title>
<link rel="stylesheet" href="https://fonts.googleapis.com/css2?family=Josefin+Sans:wght@300;400&display=swap">
<style>
  :root {
    --page-bg: #5f6d70;
    --card-white: #ffffff;
    --mint: #bdf2e2;
    --teal: #3cc4a0;
    --ink: #1f1f1f;
    --alert-red: #d8262a;
  }
  * { margin: 0; padding: 0; box-sizing: border-box; }
  html, body { width: 1200px; height: 741px; overflow: hidden; }
  body {
    background: var(--page-bg);
    font-family: "Josefin Sans", sans-serif;
    position: relative;
  }
  .card {
    position: absolute;
    left: 75px; top: 65px;
    width: 1050px; height: 611px;
    background: var(--card-white);
    overflow: hidden;
  }
  .company-name {
    position: absolute;
    left: 461px; top: 68px;
    width: 567px;
    text-align: center;
    font-weight: 400;
    font-size: 38px;
    line-height: 44px;
    color: var(--ink);
  }
  .person-name {
    position: absolute;
    left: 56px; top: 178px;
    font-size: 44px; font-weight: 400;
    color: var(--teal);
  }
  .phone {
    position: absolute;
    left: 56px; top: 244px;
    display: flex; align-items: center; gap: 12px;
    font-size: 34px; font-weight: 400; color: var(--ink);
  }
  .phone svg { width: 28px; height: 28px; fill: var(--alert-red); }
  .contact-band {
    position: absolute;
    left: 0; top: 286px;
    width: 1050px; height: 247px;
    background: var(--mint);
  }
  .band-gap {
    position: absolute;
    left: 42px; top: 0;
    width: 416px; height: 247px;
    background: var(--card-white);
  }
  .contact-list {
    position: absolute;
    left: 470px; top: 52px;
    list-style: none;
    font-size: 25px; font-weight: 300;
    color: var(--ink);
  }
  .contact-list li {
    display: flex; align-items: flex-start; gap: 22px;
    line-height: 36px;
    margin-bottom: 7px;
  }
  .contact-list svg { width: 30px; height: 30px; fill: var(--card-white); flex: none; margin-top: 2px; }
  .footer-line {
    position: absolute;
    left: 14px; top: 552px;
    width: 1022px;
    display: flex; align-items: center; gap: 10px;
  }
  .footer-line::before, .footer-line::after {
    content: ""; flex: 1; height: 2px; background: var(--mint);
  }
  .tagline {
    font-size: 37px; font-weight: 300;
    color: var(--mint);
    letter-spacing: 1px;
  }
</style>
</head>
<body>
  <article class="card">
    <p class="company-name">Delia Brunet</p>

    <h1 class="person-name">Teodoro S. Brunet</h1>
    <p class="phone">
      <svg viewBox="0 0 24 24" aria-hidden="true"><path d="M6.6 10.8a15.1 15.1 0 0 0 6.6 6.6l2.2-2.2c.3-.3.7-.4 1-.2 1.1.4 2.3.6 3.6.6.6 0 1 .4 1 1V20c0 .6-.4 1-1 1A17 17 0 0 1 3 4c0-.6.4-1 1-1h3.5c.6 0 1 .4 1 1 0 1.3.2 2.5.6 3.6.1.3 0 .7-.2 1z"/></svg>
      305 555-0147
    </p>

    <section class="contact-band">
      <div class="band-gap"></div>
      <ul class="contact-list">
        <li>
          <svg viewBox="0 0 24 24" aria-hidden="true"><path d="M12 3 2 12h3v8h5v-5h4v5h5v-8h3z"/></svg>
          <span>4180 Harbor View Ave Suite 310<br>Coral Bend FL 33099</span>
        </li>
        <li>
          <svg viewBox="0 0 24 24" aria-hidden="true"><path d="M3 5h18v14H3zm2 2v.5l7 5 7-5V7z"/></svg>
          <span>www.dbexecutivesearch.com</span>
        </li>
        <li>
          <svg viewBox="0 0 24 24" aria-hidden="true"><path d="M12 2a10 10 0 1 0 0 20 10 10 0 0 0 0-20zm-1 17.9A8 8 0 0 1 4.1 10L9 15v1a2 2 0 0 0 2 2zm6.9-2.5A2 2 0 0 0 16 16h-1v-3a1 1 0 0 0-1-1H8v-2h2a1 1 0 0 0 1-1V7h2a2 2 0 0 0 2-2v-.4a8 8 0 0 1 2.9 12.8z"/></svg>
          <span>tbrunet@dbexecutivesearch.com</span>
        </li>
      </ul>
    </section>

    <div class="footer-line"><span class="tagline">Delia Brunet Executive Search</span></div>
  </article>
</body>
</html>
```